Webdesign für Heilpraktiker
Zielgruppe
Ich bin Heilpraktiker und betreibe eine Naturheilpraxis mit den Schwerpunkten der traditionellen chinesischen Medizin (TCM). Da ganz besonders in der Philosophie (sogenannte 'Schule' des Wo Shen). Aber auch in der traditionellen Heilweise der TCM, wie Akupunktur, Heilkräutermedizin und weiteres.
Die Zielgruppe sind Menschen, die medizinische Hilfe benötigen. (Vom Kind bis zum älteren Menschen).
Aufgabenstellung
Es gibt ein Praxislogo, ein Foto von mir und ggf. ein Landschaftsbild. Ich dachte an fünf Hauptseiten mit Untergruppen. Am Ende sollte alles in Wordpress formatiert werden können, um es zu veröffentlichen.
Weitere Fotos zur Unterstützung der Themen kann ich natürlich gerne liefern.
Die Gestaltung ist nicht festgesetzt. Sollte aber seriös rüber kommen.

```html
<!DOCTYPE html>
<html lang="de">
<head>
<meta charset="utf-8">
<title>Naturheilpraxis Kellermann</title>
<link href="https://fonts.googleapis.com/css2?family=DM+Serif+Display&family=Ubuntu:wght@400;500;700&display=swap" rel="stylesheet">
<style>
:root{
  --gold:#d9ac66;
  --gold-dark:#b8884a;
  --grey:#666666;
  --ink:#1c1c1c;
  --text:#333333;
  --white:#ffffff;
}
*{margin:0;padding:0;box-sizing:border-box}
html,body{width:1200px;height:3128px;overflow:hidden;background:var(--white)}
body{position:relative;font-family:'Ubuntu',sans-serif;color:var(--text);font-size:11.5px;line-height:1.45}
.abs{position:absolute}
.serif{font-family:'DM Serif Display',serif;font-weight:400;line-height:1.15}
.dots{position:absolute;width:62px;border-top:2px dotted currentColor}
.btn{position:absolute;display:flex;align-items:center;justify-content:center;gap:7px;border-radius:20px;font-size:10.5px;font-weight:500;white-space:nowrap}
.btn svg{width:10px;height:10px}
.btn-outline{border:2px solid var(--gold-dark);color:var(--gold-dark)}
.btn-outline.dark{border-color:#6b5230;color:#6b5230}

/* hero */
.hero{left:0;top:0;width:1200px;height:482px;background:linear-gradient(180deg,#7d8a86 0%,#7f9b4f 30%,#6f9133 60%,#5c7a2c 100%)}
.topbar{top:20px;font-size:8.5px;color:var(--white);display:flex;align-items:center;gap:5px;white-space:nowrap}
.topbar svg{width:9px;height:9px;fill:var(--white)}
.nav{left:244px;top:47px;width:712px;height:62px;background:var(--white)}
.nav-item{position:absolute;top:72px;font-size:9px;font-weight:500;color:#555;white-space:nowrap}
.nav-home{left:288px;top:39px;width:41px;height:78px;background:var(--gold);border-radius:0 0 3px 3px;color:var(--white);font-size:9px;font-weight:700;display:flex;align-items:center;justify-content:center}
.brand{left:567px;top:70px;display:flex;align-items:center;gap:5px;font-size:9.5px;font-weight:500;color:var(--gold-dark);white-space:nowrap}
.brand i{display:block;width:8px;height:8px;border-radius:50%;background:var(--gold-dark)}
.hero-title{left:253px;top:166px;font-size:45px;color:var(--white);line-height:1.03}
.hero-text{left:253px;top:318px;width:380px;color:var(--white);font-size:12px;font-weight:500;line-height:1.4}
.btn-phone{left:253px;top:394px;width:121px;height:37px;background:var(--grey);color:var(--white)}
.btn-phone svg{fill:var(--white)}
.btn-contact{left:394px;top:394px;width:149px;height:37px;background:var(--gold);color:var(--white)}
.btn-contact svg{stroke:var(--white)}

/* intro */
.intro-dots{left:569px;top:526px;color:var(--gold)}
.intro-title{left:300px;top:548px;width:600px;text-align:center;font-size:24px;color:var(--gold)}
.intro-text{left:352px;top:587px;width:495px;text-align:center;font-size:11px}

/* person */
.person-band{left:0;top:707px;width:1200px;height:295px;background:var(--gold)}
.person-name{left:250px;top:788px;font-size:26px;color:var(--ink)}
.person-dots{left:250px;top:826px;color:var(--ink)}
.person-text{left:250px;top:849px;width:416px;font-size:11px;color:#2a2418}
.person-card{left:779px;top:751px;width:177px;height:336px;background:linear-gradient(180deg,#8b6b3f 0%,#5e5a52 55%,#5d5d5d 100%);border-bottom:3px solid var(--gold)}
.person-photo{left:793px;top:765px;width:147px;height:221px;border-radius:6px;background:linear-gradient(160deg,#d2d2d2 0%,#8f9094 55%,#3b4151 100%)}
.person-caption{left:789px;top:1015px;width:157px;text-align:center;color:var(--white);font-size:10px;line-height:1.3}
.btn-person{left:576px;top:1026px;width:139px;height:38px}

/* help */
.help-img-small{left:250px;top:1164px;width:171px;height:176px;background:linear-gradient(135deg,#e8c98c 0%,#d9893f 50%,#b65a3c 75%,#e5c07a 100%)}
.help-img-large{left:443px;top:1138px;width:258px;height:284px;background:linear-gradient(140deg,#e6a23a 0%,#d4683e 35%,#c9a2c4 60%,#6a9a8a 80%,#e6c98a 100%)}
.help-caption{left:250px;top:1371px;font-size:12.5px;font-weight:500;color:var(--ink);line-height:1.2}
.help-caption small{display:block;font-size:9px;font-weight:400}
.help-title{left:751px;top:1166px;width:200px;font-size:26px;color:var(--gold)}
.help-dots{left:751px;top:1238px;color:var(--gold)}
.help-text{left:751px;top:1259px;width:195px;font-size:11px}
.btn-help{left:751px;top:1354px;width:125px;height:39px}

/* tcm */
.tcm-band{left:0;top:1484px;width:1200px;height:366px;background:linear-gradient(180deg,#9cb2b8 0%,#2f4a2a 20%,#24482f 45%,#3f8a6a 65%,#8a9a7a 100%)}
.tcm-box{left:360px;top:1539px;width:480px;height:257px;background:rgba(38,34,22,.72)}
.tcm-title{left:425px;top:1575px;width:350px;text-align:center;font-size:24px;color:var(--gold)}
.tcm-dots{left:569px;top:1648px;color:var(--gold)}
.tcm-text{left:400px;top:1668px;width:400px;text-align:center;font-size:11px;color:var(--white)}
.tcm-text p+p{margin-top:14px}

/* first visit */
.visit-title{left:253px;top:1950px;font-size:24px;color:var(--gold)}
.visit-dots{left:253px;top:1998px;color:var(--gold)}
.visit-text{left:253px;top:2018px;width:285px;font-size:11px}
.btn-visit{left:253px;top:2115px;width:108px;height:37px}
.visit-img{left:619px;top:1908px;width:318px;height:282px}

/* wo shen */
.wo-band{left:0;top:2270px;width:1200px;height:306px;background:var(--grey)}
.wo-img{left:249px;top:2223px;width:282px;height:398px;border-radius:40% 30% 45% 35%;background:linear-gradient(160deg,#e4d3b0 0%,#c9b083 50%,#9c8258 100%)}
.wo-title{left:572px;top:2316px;font-size:24px;color:var(--gold)}
.wo-dots{left:572px;top:2364px;color:var(--gold)}
.wo-text{left:572px;top:2383px;width:368px;font-size:11px;color:var(--white)}
.btn-wo{left:572px;top:2494px;width:125px;height:38px;border-color:var(--gold);color:var(--gold)}

/* contact */
.contact-box{left:244px;top:2671px;width:420px;height:318px;background:var(--gold)}
.contact-photo{left:664px;top:2671px;width:292px;height:318px;background:linear-gradient(160deg,#d6d6d6 0%,#a5a6aa 55%,#343a48 100%)}
.contact-title{left:306px;top:2726px;font-size:24px;color:var(--ink)}
.contact-dots{left:306px;top:2765px;color:var(--ink)}
.contact-text{left:306px;top:2787px;width:300px;font-size:10.5px;line-height:1.4;color:#2a2418}
.btn-contact-now{left:306px;top:2896px;width:175px;height:38px}

/* footer */
.footer-line{top:3052px;height:1px;background:#e2e2e2}
.footer-text{top:3083px;font-size:8.5px;color:var(--ink)}
</style>
</head>
<body>

<!-- Hero -->
<div class="abs hero" role="img" aria-label="Landschaftsfoto: grüne Berghänge und Täler unter bewölktem Himmel"></div>
<div class="abs topbar" style="left:250px">
  <svg viewBox="0 0 10 10"><path d="M1 3h8v5H1z" fill="none" stroke="#fff" stroke-width="1"/><path d="M1 3l4 3 4-3" fill="none" stroke="#fff" stroke-width="1"/></svg>
  info@heilpraktiker-kellermann.de
</div>
<div class="abs topbar" style="left:410px">
  <svg viewBox="0 0 10 10"><path d="M2 1l2 0 1 2.5-1.2 1a5 5 0 0 0 2.2 2.2l1-1.2L9.5 6.5v2a1 1 0 0 1-1 1A8 8 0 0 1 1 2a1 1 0 0 1 1-1z"/></svg>
  0987 654 3210
</div>
<div class="abs topbar" style="left:793px">
  <svg viewBox="0 0 10 10"><path d="M5 0a3.3 3.3 0 0 1 3.3 3.3C8.3 6 5 10 5 10S1.7 6 1.7 3.3A3.3 3.3 0 0 1 5 0z"/><circle cx="5" cy="3.3" r="1.2" fill="#7f9b4f"/></svg>
  Lindenweg 8 - 54321 Beispielstadt
</div>

<div class="abs nav"></div>
<div class="abs nav-home">Home</div>
<div class="nav-item" style="left:336px">Zu meiner Person</div>
<div class="nav-item" style="left:427px">Wobei kann ich helfen</div>
<div class="abs brand"><i></i>Kellermann</div>
<div class="nav-item" style="left:683px">Der erste Besuch</div>
<div class="nav-item" style="left:772px">Was ist das Wo Shen</div>
<div class="nav-item" style="left:878px">Kontakt</div>

<h1 class="abs serif hero-title">Herzlich<br>Willkommen<br>Muster Titel</h1>
<p class="abs hero-text">Muster Text Lorem ipsum dolor sit amet consetetur sadipscing elitr, sed diam nonumy eirmod tempor invidunt ut labore et dolore magna aliquyam erat, sed diam voluptua.</p>
<div class="btn btn-phone">0987 6543210
  <svg viewBox="0 0 10 10"><path d="M2 1l2 0 1 2.5-1.2 1a5 5 0 0 0 2.2 2.2l1-1.2L9.5 6.5v2a1 1 0 0 1-1 1A8 8 0 0 1 1 2a1 1 0 0 1 1-1z"/></svg>
</div>
<div class="btn btn-contact">Kontakt aufnehmen
  <svg viewBox="0 0 10 10" fill="none" stroke-width="1.4"><path d="M1 5h8M6 2l3 3-3 3"/></svg>
</div>

<!-- Intro -->
<div class="dots intro-dots"></div>
<h2 class="abs serif intro-title">Naturheilpraxis Kellermann</h2>
<p class="abs intro-text">Muster text Lorem ipsum dolor sit amet, consetetur sadipscing elitr, sed diam nonumy eirmod tempor invidunt ut labore et dolore magna aliquyam erat, sed diam voluptua. At vero eos et accusam et justo duo dolores et ea rebum. Stet clita kasd gubergren, no sea takimata sanctus est Lorem ipsum dolor sit amet. Lorem ipsum dolor sit amet, consetetur sadipscing elitr, sed diam nonumy eirmod tempor invidunt ut labore et dolore magna aliquyam erat.</p>

<!-- Person -->
<div class="abs person-band"></div>
<h2 class="abs serif person-name">Matthias Kellermann</h2>
<div class="dots person-dots"></div>
<p class="abs person-text">Seit vielen Jahrzehnten begeistere ich mich für die Themen der Medizin und die Wiederherstellung der Gesundheit.<br>Ein grundlegendes Gesundheitssystem habe ich schon immer in der traditionellen chinesischen Medizin gesehen...</p>
<div class="abs person-card"></div>
<div class="abs person-photo" role="img" aria-label="Porträtfoto des Heilpraktikers"></div>
<p class="abs person-caption">Heilpraktiker und zertifizierter Therapeut der traditionellen chinesischen Medizin (Berufsverband NHV e.V.)</p>
<div class="btn btn-outline dark btn-person">Zu meiner Person
  <svg viewBox="0 0 10 10" fill="none" stroke="currentColor" stroke-width="1.4"><path d="M1 5h8M6 2l3 3-3 3"/></svg>
</div>

<!-- Help -->
<div class="abs help-img-small" role="img" aria-label="Farbige abstrakte Malerei in Gelb-, Orange- und Rottönen"></div>
<div class="abs help-img-large" role="img" aria-label="Farbige abstrakte Malerei mit Kreisen in Orange, Violett und Grün"></div>
<p class="abs help-caption">Muster Text Lorem ipsum<small>Consetetur sadipscing elitr sed</small></p>
<h2 class="abs serif help-title">Wobei kann ich helfen</h2>
<div class="dots help-dots"></div>
<p class="abs help-text">Der Schwerpunkt meiner Tätigkeit ist die Beseitigung und Linderung von chronischen Erkrankungen und deren Folgen. Diese biete ich verschiedene Therapieformen...</p>
<div class="btn btn-outline dark btn-help">mehr erfahren
  <svg viewBox="0 0 10 10" fill="none" stroke="currentColor" stroke-width="1.4"><path d="M1 5h8M6 2l3 3-3 3"/></svg>
</div>

<!-- TCM -->
<div class="abs tcm-band" role="img" aria-label="Landschaftsfoto: Bergsee mit Nadelwald am Ufer"></div>
<div class="abs tcm-box"></div>
<h2 class="abs serif tcm-title">Die Traditionelle Chinesische Medizin</h2>
<div class="dots tcm-dots"></div>
<div class="abs tcm-text">
  <p>Leiden Sie unter chronischen Schmerzen? Haben Sie eine Autoimmunerkrankung? Wollen Sie wieder den Frühling genießen ohne Heuschnupfen? Sind Sie gestresst bei der Arbeit oder in der Familie?</p>
  <p>Vertrauen Sie Ihrem eigenen Körper! Beginnen Sie die Behandlung mit einer nebenwirkungsarmen Methode.</p>
</div>

<!-- First visit -->
<h2 class="abs serif visit-title">Der erste Besuch</h2>
<div class="dots visit-dots"></div>
<p class="abs visit-text">Am Anfang steht eine einstündige Anamnese mit ausführlicher Interpretation ihrer bisherigen Untersuchungsergebnisse und Laborberichten. Gegebenenfalls werden weitere Laboraufträge zur Diagnosesicherung und Verlaufskontrolle beauftragt...</p>
<div class="btn btn-outline dark btn-visit">mehr dazu
  <svg viewBox="0 0 10 10" fill="none" stroke="currentColor" stroke-width="1.4"><path d="M1 5h8M6 2l3 3-3 3"/></svg>
</div>
<svg class="abs visit-img" viewBox="0 0 318 282" role="img" aria-label="Foto: Mörser und getrocknete Heilkräuter">
  <defs>
    <linearGradient id="herbs" x1="0" y1="0" x2="1" y2="1">
      <stop offset="0" stop-color="#3a2416"/>
      <stop offset=".5" stop-color="#8a4a26"/>
      <stop offset="1" stop-color="#d8b98c"/>
    </linearGradient>
  </defs>
  <path d="M4 150 A155 155 0 0 1 314 150" fill="none" stroke="#111" stroke-width="4"/>
  <path d="M10 150 A149 149 0 0 1 308 150 L302 205 L232 272 L86 272 L16 205 Z" fill="url(#herbs)"/>
  <path d="M16 205 L86 272 L232 272 L302 205" fill="none" stroke="#555" stroke-width="3"/>
</svg>

<!-- Wo Shen -->
<div class="abs wo-band"></div>
<div class="abs wo-img" role="img" aria-label="Großes chinesisches Schriftzeichen aus alter Buchseite"></div>
<h2 class="abs serif wo-title">Was ist das Wo Shen</h2>
<div class="dots wo-dots"></div>
<p class="abs wo-text">Das Wo Shen ist aus unserer heutigen Sicht ein Ratgeber für ein harmonisches und gesundes Sein, im Zusammenleben mit allen Lebensformen. Es war in all den Jahrtausenden unter anderem ein Anleitungsbuch zum Befragen eines Orakels, eine Handlungsanweisung für chinesische Beamte im 17. Jahrhundert, ein medizinischer Ratgeber, ein Buch über Weltanschauungen und vieles, vieles mehr...</p>
<div class="btn btn-outline btn-wo">mehr erfahren
  <svg viewBox="0 0 10 10" fill="none" stroke="currentColor" stroke-width="1.4"><path d="M1 5h8M6 2l3 3-3 3"/></svg>
</div>

<!-- Contact -->
<div class="abs contact-box"></div>
<div class="abs contact-photo" role="img" aria-label="Porträtfoto des Heilpraktikers"></div>
<h2 class="abs serif contact-title">Kontakt aufnehmen</h2>
<div class="dots contact-dots"></div>
<p class="abs contact-text">Muster Text Lorem ipsum dolor sit amet, consetetur sadipscing elitr, sed diam nonumy eirmod tempor invidunt ut labore et dolore magna aliquyam erat, sed diam voluptua. At vero eos et accusam et justo duo dolores et ea rebum. Stet clita kasd gubergren, no sea takimata sanctus est Lorem ipsum dolor sit amet. Lorem ipsum dolor sit amet.</p>
<div class="btn btn-outline dark btn-contact-now">Jetzt Kontakt aufnehmen
  <svg viewBox="0 0 10 10" fill="none" stroke="currentColor" stroke-width="1.4"><path d="M1 5h8M6 2l3 3-3 3"/></svg>
</div>

<!-- Footer -->
<div class="abs footer-line" style="left:253px;width:339px"></div>
<div class="abs footer-line" style="left:609px;width:338px"></div>
<p class="abs footer-text" style="left:253px">© 2022 Heilpraktiker Kellermann. Alle Rechte vorbehalten</p>
<p class="abs footer-text" style="left:846px">Impressum / Datenschutz</p>

</body>
</html>
```